RTavenor Business Cards & Letterhead

I have a logo but need a design for some new business cards. We are a Design-Build Firm that specializes in the design and construction of commercial projects.
the cards need to be professional. no cartoon stuff.
i would like to have the cards in AI format so I can update the card as needed. Logo is provided.
Our Address is: 4187 Marlowe Ct. Ashford Vale, Oregon 27614

```html
<!DOCTYPE html>
<html lang="en">
<head>
<meta charset="UTF-8">
<title>RTavenor Business Card</title>
<link href="https://fonts.googleapis.com/css2?family=Roboto:wght@400;700;900&display=swap" rel="stylesheet">
<style>
  :root {
    --backdrop: #979797;
    --brand-blue: #0068a3;
    --card-white: #ffffff;
    --ink-grey: #555759;
  }
  * { margin: 0; padding: 0; box-sizing: border-box; }
  html, body {
    width: 1200px;
    height: 1000px;
    overflow: hidden;
  }
  body {
    background: var(--backdrop);
    font-family: "Roboto", Arial, sans-serif;
    position: relative;
  }
  .card {
    position: absolute;
    left: 293px;
    width: 615px;
    height: 351px;
  }
  .card-front {
    top: 110px;
    background: var(--brand-blue);
    border-radius: 32px 32px 162px 22px;
  }
  .card-back {
    top: 519px;
    background: var(--card-white);
    border-radius: 32px 32px 20px 162px;
  }
  .wordmark {
    position: absolute;
    display: flex;
    align-items: center;
    font-weight: 900;
    text-transform: uppercase;
    white-space: nowrap;
  }
  .wordmark-mark {
    display: inline-block;
  }
  .card-front .wordmark {
    left: 0; right: 0;
    top: 153px;
    justify-content: center;
    color: var(--card-white);
    font-size: 52px;
    letter-spacing: 2px;
    gap: 12px;
  }
  .card-front .wordmark-mark {
    width: 34px; height: 34px;
    background: var(--card-white);
  }
  .card-back .wordmark {
    left: 0; right: 0;
    top: 39px;
    justify-content: center;
    color: var(--ink-grey);
    font-size: 38px;
    letter-spacing: 1.5px;
    gap: 9px;
  }
  .card-back .wordmark-mark {
    width: 24px; height: 24px;
    background: var(--ink-grey);
  }
  .person {
    position: absolute;
    right: 326px;
    top: 157px;
    text-align: right;
    font-size: 16px;
    line-height: 19px;
  }
  .person-name {
    color: var(--brand-blue);
    font-weight: 700;
  }
  .person-role {
    color: var(--ink-grey);
  }
  .divider {
    position: absolute;
    left: 306px;
    top: 149px;
    width: 3px;
    height: 53px;
    background: var(--brand-blue);
  }
  .contact {
    position: absolute;
    left: 325px;
    top: 147px;
    list-style: none;
    color: var(--ink-grey);
    font-size: 16px;
    line-height: 19px;
  }
  .address {
    position: absolute;
    left: 142px;
    top: 292px;
    color: var(--ink-grey);
    font-size: 16px;
  }
</style>
</head>
<body>
  <section class="card card-front" aria-label="Card front">
    <div class="wordmark"><span class="wordmark-mark"></span>RTavenor</div>
  </section>

  <section class="card card-back" aria-label="Card back">
    <div class="wordmark"><span class="wordmark-mark"></span>RTavenor</div>

    <div class="person">
      <div class="person-name">ROLAND TAVENOR</div>
      <div class="person-role">Founder/President</div>
    </div>
    <div class="divider"></div>
    <ul class="contact">
      <li>555-201-0148</li>
      <li>roland@rtavenor.com</li>
      <li>www.rtavenor.com</li>
    </ul>

    <p class="address">4187 Marlowe Ct. Ashford Vale, Oregon 27614</p>
  </section>
</body>
</html>
```